Sonic Vale

Rebrand current website and move it to SonicVale.com. Looking for a professional, eye catching, top 10 in World type website. My current website is: https://madebytorven.sitepadhub.com/sonicvale
I would like it moved to sonicvale.com.

```html
<!DOCTYPE html>
<html lang="en">
<head>
<meta charset="utf-8">
<title>Sonic Vale — Music Producer Portfolio</title>
<link rel="stylesheet" href="https://fonts.googleapis.com/css2?family=Montserrat:wght@700;800&family=Roboto:ital,wght@0,400;0,500;0,700;1,500&display=swap">
<style>
:root{
  --ink:#0d101c;
  --about:#131729;
  --panel-a:#1d2134;
  --panel-b:#272c42;
  --player:#10131f;
  --magenta:#9a1290;
  --blue:#1f86e0;
  --white:#ffffff;
  --muted:#c4c7d3;
}
*{margin:0;padding:0;box-sizing:border-box}
html,body{width:1200px;height:3508px;overflow:hidden;background:var(--ink)}
body{position:relative;font-family:"Roboto",sans-serif;color:var(--white)}
.abs{position:absolute}
.head{font-family:"Montserrat",sans-serif;font-weight:800;letter-spacing:1px}
.accent{color:var(--blue)}
.btn{position:absolute;display:flex;align-items:center;justify-content:center;background:var(--magenta);color:var(--white);border-radius:32px;font-weight:700;font-size:15px;letter-spacing:.3px}

/* hero */
.hero{left:0;top:0;width:1200px;height:667px;background:radial-gradient(ellipse at 50% 40%,#2a3350 0%,#171c2e 55%,#0c0f19 100%)}
.logo{left:146px;top:34px;font-family:"Montserrat",sans-serif;font-weight:700;font-size:34px}
.nav{top:50px;font-size:14px;font-weight:500}
.nav-active{border-bottom:3px solid var(--magenta);padding-bottom:6px}
.hero-title{left:0;width:1200px;text-align:center;font-size:68px;line-height:82px;top:212px}
.hero-sub{left:0;width:1200px;text-align:center;top:399px;font-size:23px;font-weight:500}

/* about */
.about{left:0;top:667px;width:1200px;height:382px;background:var(--about)}
.about-title{left:158px;top:722px;font-size:46px}
.about-text{left:158px;top:806px;width:520px;font-size:13.5px;line-height:24px;color:var(--muted)}
.about-photo{left:724px;top:695px;width:318px;height:318px;border-radius:50%;background:radial-gradient(circle at 45% 40%,#5a8fd0 0%,#7b3aa6 45%,#2a1f4a 80%);box-shadow:8px -4px 0 0 var(--blue)}

/* products */
.prod{top:1049px;height:377px;width:600px}
.prod-icon{width:170px;height:170px;border:3px solid #6b6e7c;border-radius:50%;top:1135px}
.prod-title{font-size:26px;font-weight:500;top:1128px}
.prod-price{font-size:22px;color:var(--blue);top:1172px}
.prod-desc{font-size:13.5px;line-height:24px;color:var(--muted);top:1210px;width:320px}

/* player */
.stage{left:0;top:1426px;width:1200px;height:778px;background:linear-gradient(160deg,#3a3e52 0%,#262a3a 45%,#1b1e2b 100%)}
.player{left:144px;top:1467px;width:910px;height:595px;background:var(--player);border:1px solid #1f2333}
.player-head{left:0;top:0;width:908px;height:146px;border-bottom:1px solid #22263a}
.track{left:46px;width:820px;font-size:13px;color:#d6d8e0;display:flex;align-items:center;height:20px}
.track .rule{flex:1;border-bottom:1px dashed #2c3044;margin:0 40px 0 50px;height:1px}
.pager{width:44px;height:44px;border:2px solid #8d90a0;border-radius:50%;top:2108px}

/* services */
.services-title{left:0;width:1200px;text-align:center;top:2286px;font-size:46px}
.svc-icon{width:104px;height:104px;border-radius:50%;background:var(--magenta);top:2417px}
.svc-text{font-size:32px;font-weight:500;line-height:37px;top:2434px}

/* quote */
.quote-bg{left:0;top:2615px;width:1200px;height:650px;background:linear-gradient(135deg,#8e1590 0%,#a61aa0 50%,#6c0e6e 100%)}
.quote-box{left:222px;top:2768px;width:756px;height:340px;background:rgba(120,10,115,.55);border:1px solid rgba(255,255,255,.12)}
.quote-mark{left:0;width:1200px;text-align:center;top:2790px;font-size:120px;line-height:120px;color:var(--blue);font-weight:700}
.quote-text{left:222px;width:756px;top:2896px;text-align:center;font-size:32px;line-height:48px;font-style:italic;font-weight:500}
.quote-author{left:0;width:1200px;text-align:center;top:3020px;font-size:38px;font-weight:700}

/* footer */
.contact{left:0;width:1200px;top:3318px;display:flex;justify-content:center;align-items:center;gap:12px;font-size:26px}
.copy{left:0;width:1200px;top:3385px;text-align:center;font-size:13px;color:#d0d2dc}
.social{left:0;width:1200px;top:3440px;display:flex;justify-content:center;gap:26px;font-size:16px;font-weight:700;color:var(--blue)}
</style>
</head>
<body>

<svg width="0" height="0" style="position:absolute">
  <symbol id="share" viewBox="0 0 12 12"><g fill="#fff"><circle cx="2.5" cy="6" r="2"/><circle cx="9.5" cy="2.5" r="2"/><circle cx="9.5" cy="9.5" r="2"/></g><path d="M2.5 6l7-3.5M2.5 6l7 3.5" stroke="#fff" stroke-width="1.2"/></symbol>
</svg>

<!-- hero -->
<div class="abs hero" role="img" aria-label="Producer seated at a large studio mixing console, dark blue lighting"></div>
<div class="abs logo">Sonic Vale</div>
<div class="abs nav nav-active" style="left:740px">HOME</div>
<div class="abs nav" style="left:817px">SHOP</div>
<div class="abs nav" style="left:892px">BOOK ONLINE</div>
<div class="abs nav" style="left:1020px">BLOG</div>
<h1 class="abs head hero-title"><span class="accent">JOURNEY</span> WITH<br>SONIC VALE</h1>
<div class="abs hero-sub">Music Producer Portfolio</div>
<div class="btn" style="left:507px;top:466px;width:186px;height:60px">GET STARTED</div>
<svg class="abs" style="left:577px;top:588px" width="46" height="46" viewBox="0 0 46 46" fill="none" stroke="#fff" stroke-width="2"><circle cx="23" cy="23" r="21"/><path d="M23 12v21M15 25l8 8 8-8"/></svg>

<!-- about -->
<section class="abs about"></section>
<h2 class="abs head about-title">ABOUT <span class="accent">ME</span></h2>
<p class="abs about-text">Hailing from Port Alden, Corwin has always pushed himself to achieve more success in his music career. Looking to perfect his technical abilities and develop his own unique style, Corwin draws upon his Port Alden roots and lifelong passion for music. Get in touch to learn more about his background, experience, and latest projects.</p>
<div class="btn" style="left:158px;top:928px;width:164px;height:60px">GET IN TOUCH</div>
<div class="abs about-photo" role="img" aria-label="DJ performing at decks under purple and blue club lights"></div>

<!-- products -->
<div class="abs prod" style="left:0;background:var(--panel-a)"></div>
<div class="abs prod" style="left:600px;background:var(--panel-b)"></div>

<div class="abs prod-icon" style="left:44px"></div>
<svg class="abs" style="left:74px;top:1182px" width="110" height="80" viewBox="0 0 110 80" fill="none" stroke="#fff" stroke-width="2.5"><rect x="3" y="4" width="70" height="70"/><path d="M73 14a26 26 0 0 1 0 50"/><path d="M73 24a16 16 0 0 1 0 30"/><circle cx="73" cy="39" r="4"/></svg>
<div class="abs prod-title" style="left:252px">MIXING AND MASTERING</div>
<div class="abs prod-price" style="left:252px">$150.00</div>
<div class="abs prod-desc" style="left:252px">Get your music mix and mastered professionally to industry standards.</div>
<div class="btn" style="left:252px;top:1282px;width:164px;height:60px">ADD TO CART</div>

<div class="abs prod-icon" style="left:644px"></div>
<svg class="abs" style="left:690px;top:1165px" width="80" height="112" viewBox="0 0 80 112" fill="none" stroke="#fff" stroke-width="2.5"><path d="M5 18h70v74l-16 16H5z"/><path d="M59 108V92h16"/><path d="M20 18V6h8v12M52 18V6h8v12"/><path d="M28 76l12-34 12 34M32 64h16"/></svg>
<div class="abs prod-title" style="left:848px">BOOK A SESSION</div>
<div class="abs prod-price" style="left:848px">$150.00</div>
<div class="abs prod-desc" style="left:848px">Get your music mix and mastered professionally to industry standards.</div>
<div class="btn" style="left:848px;top:1282px;width:164px;height:60px">ADD TO CART</div>

<!-- player -->
<div class="abs stage" role="img" aria-label="Studio desk with keyboard, drum pads and mixer seen from above, dimmed"></div>
<div class="abs player">
  <div class="abs player-head"></div>
  <div class="abs" style="left:11px;top:31px;width:72px;height:72px;border-radius:50%;background:linear-gradient(135deg,#c98a4a,#6b3a22)" role="img" aria-label="Artist avatar"></div>
  <div class="abs head" style="left:98px;top:35px;font-size:20px;letter-spacing:.5px">CORWIN</div>
  <div class="abs" style="left:98px;top:66px;font-size:9px;color:#c8cad4">cv</div>
  <div class="abs" style="left:98px;top:81px;font-size:9px;color:#c8cad4">FIRST LIGHT (Remastered)</div>
  <svg class="abs" style="left:290px;top:61px" width="50" height="12" viewBox="0 0 50 12" fill="#fff"><rect x="0" y="1" width="2" height="10"/><path d="M9 1v10L3 6z"/><rect x="18" y="1" width="2" height="10"/><path d="M21 1v10l6-5z"/><path d="M37 1v10l9-5z"/></svg>
  <div class="abs" style="left:423px;top:61px;font-size:10px;color:#c8cad4">00:0000: / 02:0900:02:09</div>
  <svg class="abs" style="left:648px;top:60px" width="56" height="14" viewBox="0 0 56 14" fill="#fff"><path d="M0 4h3l4-3v12l-4-3H0z"/><path d="M9 4a4 4 0 0 1 0 6" stroke="#fff" fill="none"/><path d="M27 2l6-1v9a2 2 0 1 1-1-2V3l-4 1v7a2 2 0 1 1-1-2z"/><circle cx="44" cy="7" r="2"/><circle cx="51" cy="3" r="2"/><circle cx="51" cy="11" r="2"/><path d="M44 7l7-4M44 7l7 4" stroke="#fff"/></svg>
  <div class="abs" style="left:292px;top:96px;width:412px;height:6px;border-radius:3px;background:#2e3348"></div>
  <div class="btn" style="left:775px;top:56px;width:125px;height:46px;font-size:11px">Single $200.00</div>
</div>
<div class="abs" style="left:144px;top:1653px;width:910px">
  <div class="abs track" style="top:0"><span>1Low Tide / Corwin</span><span class="rule"></span><svg width="12" height="12"><use href="#share"/></svg></div>
  <div class="abs track" style="top:39px"><span>2 B side / Corwin</span><span class="rule"></span><svg width="12" height="12"><use href="#share"/></svg></div>
  <div class="abs track" style="top:78px"><span>3 K Loop / Corwin</span><span class="rule"></span><svg width="12" height="12"><use href="#share"/></svg></div>
  <div class="abs track" style="top:117px"><span>4 Monsoon / Corwin</span><span class="rule"></span><svg width="12" height="12"><use href="#share"/></svg></div>
  <div class="abs track" style="top:156px"><span>5 Drifter / Corwin</span><span class="rule"></span><svg width="12" height="12"><use href="#share"/></svg></div>
  <div class="abs track" style="top:195px"><span>6 velvet / Corwin</span><span class="rule"></span><svg width="12" height="12"><use href="#share"/></svg></div>
  <div class="abs track" style="top:234px"><span>7 on road / Corwin</span><span class="rule"></span><svg width="12" height="12"><use href="#share"/></svg></div>
  <div class="abs track" style="top:273px"><span>8 Shore to Shore / Corwin</span><span class="rule"></span><svg width="12" height="12"><use href="#share"/></svg></div>
  <div class="abs track" style="top:312px"><span>9 hold Still / Corwin</span><span class="rule"></span><svg width="12" height="12"><use href="#share"/></svg></div>
  <div class="abs track" style="top:351px"><span>10 Rivera / Corwin</span><span class="rule"></span><svg width="12" height="12"><use href="#share"/></svg></div>
</div>
<svg class="abs pager" style="left:549px" viewBox="0 0 44 44" fill="none" stroke="#c9cbd6" stroke-width="2"><path d="M25 14l-8 8 8 8"/></svg>
<svg class="abs pager" style="left:606px" viewBox="0 0 44 44" fill="none" stroke="#c9cbd6" stroke-width="2"><path d="M19 14l8 8-8 8"/></svg>

<!-- services -->
<h2 class="abs head services-title">OUR <span class="accent">SERVICES</span></h2>
<div class="abs svc-icon" style="left:186px"></div>
<svg class="abs" style="left:208px;top:2440px" width="60" height="58" viewBox="0 0 60 58" fill="none" stroke="#fff" stroke-width="2.5"><rect x="5" y="22" width="50" height="32" rx="2"/><path d="M5 22l46-12-2-8L3 14z"/><path d="M14 11l5 7M26 8l5 7M38 5l5 7"/><path d="M5 30h50"/><path d="M25 36v12l10-6z"/></svg>
<div class="abs svc-text" style="left:312px">Music production<br>for movies</div>
<div class="abs svc-icon" style="left:638px"></div>
<svg class="abs" style="left:662px;top:2440px" width="56" height="58" viewBox="0 0 56 58" fill="#fff"><path d="M20 4h26v50H20z" fill="none" stroke="#fff" stroke-width="2.5"/><path d="M6 22h14v32H6z" fill="none" stroke="#fff" stroke-width="2.5"/><rect x="25" y="10" width="5" height="5"/><rect x="36" y="10" width="5" height="5"/><rect x="25" y="20" width="5" height="5"/><rect x="36" y="20" width="5" height="5"/><rect x="25" y="30" width="5" height="5"/><rect x="36" y="30" width="5" height="5"/><rect x="10" y="28" width="5" height="5"/><rect x="10" y="38" width="5" height="5"/><rect x="29" y="42" width="8" height="12"/></svg>
<div class="abs svc-text" style="left:764px">Music production<br>for commercials</div>

<!-- quote -->
<div class="abs quote-bg" role="img" aria-label="Producer working at a keyboard and monitor in a studio, magenta tint"></div>
<div class="abs quote-box"></div>
<div class="abs quote-mark">”</div>
<p class="abs quote-text">“Music expresses that which cannot be said and<br>on which it is impossible to be silent”</p>
<div class="abs quote-author">MARCEL AUBRY</div>

<!-- footer -->
<div class="abs contact">
  <svg width="16" height="22" viewBox="0 0 16 22" fill="var(--magenta)"><path d="M8 0a8 8 0 0 1 8 8c0 6-8 14-8 14S0 14 0 8a8 8 0 0 1 8-8z"/><circle cx="8" cy="8" r="3" fill="var(--ink)"/></svg>
  <span>Port Alden,Louisiana</span><span>|</span>
  <svg width="26" height="18" viewBox="0 0 26 18" fill="var(--magenta)"><rect width="26" height="18" rx="2"/><path d="M1 2l12 9 12-9" stroke="var(--ink)" stroke-width="2" fill="none"/></svg>
  <span>producedbycorwin@mailbox.com</span><span>|</span>
  <svg width="20" height="20" viewBox="0 0 20 20" fill="var(--magenta)"><path d="M4 0l4 5-2 3c1 3 3 5 6 6l3-2 5 4-3 4C8 20 0 12 0 3z"/></svg>
  <span>555-010-2234</span>
</div>
<div class="abs copy">©2021 by Sonic Vale . All Rights Reserved &nbsp;|&nbsp; Privacy Policy</div>
<div class="abs social"><span>Pagefold</span><span>Workwire</span><span>Pixgram</span></div>

</body>
</html>
```